Growing Plumbing company requires signage for vans/trucks plus letterhead and business cards

Pelkey's Plumbing and Heating (see www.pelkeysnf.ca) is a well established plumbing and heating company that has been servicing the new construction, renovation and plumbing maintenance needs of residential and commercial clients for over 40 years. It operates in St. John's, Newfoundland and Labrador, Canada..

The company is now expanding into a new line of business (electrical contracting) and requires a slight modification to its existing logo. The change is from "Pelkey's Plumbing and Heating" to "Pelkey's Plumbing and Electrical". An existing raw data file is provided to allow for this slight change. NO OTHER CHANGE TO THE LOGO IS REQUIRED.

As a result of this logo change, the company would like to create a new corporate identity package that includes the following:

- Signage for company vans (sample provided with new suggestions requested)

- Signage for company trucks (simple sign on driver and passenger doors and on tailgate) (no sample exists).

- Corporate letter head (sample provided with new suggestions requested)

- Business cards (sample provided with new suggestions requested)
Updates

Hello all, 

To clarify: work on the corporate logo only requires the word change from "Heating" to "Electric". No other changes are requested on the logo. ie no changes to "D", etc. 

As a result of this slight logo change, we are also requesting suggestions that could be made to existing corporate signage, letterhead, etc. 

Thanks, 

The Pelkey's Team. 

The exact font files to be used have been uploaded.

To clarify on corporate name: 

It is to be "Pelkey's Plumbing and Electrical"   (Not Heating or Electric)

The Pelkey's Team

Industry/Entity Type

Residential

Logo Text

Pelkey's Plumbing and Electrical

Requirements
Must have
• For van and truck signage, we want something that is "clean". Phone number, website, and logo must be included.

For logo, except for change from "heating" to "electrical" no other changes are requested.

For the logo change, we will require logo to be provided for all reproduction requirements including vertical (stacked) and horizontal treatments; black & white / colour / reverse; file formats including vector (designer use) and jpeg/pdf/gif, etc. (user use); variety of sizes in all files (i.e. small, medium and large).
Nice to have
• An idea would be to have the business cards, signage and letterhead use the grey bars in the "D" of the logo as a background or to the side.

```html
<!DOCTYPE html>
<html lang="en">
<head>
<meta charset="utf-8">
<title>Pelkey's Plumbing and Electrical – Van Rear Signage</title>
<link rel="stylesheet" href="https://fonts.googleapis.com/css2?family=Archivo:wdth,wght@62..125,700&display=swap">
<style>
  :root {
    --brand-blue: #0f4a7f;
    --sign-white: #ffffff;
    --page-bg: #ffffff;
  }
  * { margin: 0; padding: 0; box-sizing: border-box; }
  html, body {
    width: 1200px;
    height: 900px;
    overflow: hidden;
    background: var(--page-bg);
  }
  .signage {
    position: relative;
    width: 1200px;
    height: 900px;
    font-family: "Archivo", Arial, sans-serif;
    font-weight: 700;
  }
  .brand {
    position: absolute;
    left: 365px;
    top: 224px;
    display: flex;
    align-items: center;
    gap: 36px;
  }
  .brand-mark {
    width: 86px;
    height: 86px;
    background: var(--brand-blue);
  }
  .brand-name {
    color: var(--brand-blue);
    font-weight: 700;
    line-height: 1;
    text-transform: uppercase;
  }
  .brand-name .brand-word {
    display: block;
    font-size: 62px;
    font-stretch: 125%;
    letter-spacing: 0;
  }
  .brand-name .brand-trade {
    display: block;
    font-size: 24px;
    letter-spacing: 0.3px;
    margin-top: 4px;
  }
  .tagline {
    position: absolute;
    left: 362px;
    top: 386px;
    font-size: 17px;
    color: var(--brand-blue);
    text-transform: uppercase;
    letter-spacing: 0.3px;
  }
  .contact-band {
    position: absolute;
    left: 333px;
    top: 429px;
    width: 550px;
    height: 56px;
    background: var(--brand-blue);
  }
  .phone {
    position: absolute;
    left: 30px;
    top: 9px;
    font-size: 32px;
    color: var(--sign-white);
    letter-spacing: 1.5px;
  }
  .website {
    position: absolute;
    left: 358px;
    top: 493px;
    font-size: 26px;
    color: var(--brand-blue);
    letter-spacing: 0.3px;
  }
</style>
</head>
<body>
  <main class="signage">
    <div class="brand">
      <div class="brand-mark" aria-hidden="true"></div>
      <h1 class="brand-name">
        <span class="brand-word">Pelkey's</span>
        <span class="brand-trade">Plumbing and Electrical</span>
      </h1>
    </div>
    <p class="tagline">Serving the local community for over 40 years</p>
    <div class="contact-band">
      <p class="phone">709 555 0142</p>
    </div>
    <p class="website">www.pelkeysnf.ca</p>
  </main>
</body>
</html>
```